New Business Card Design Project

I need a design for business cards, i am an electrical business called "Corvane Electrical and Communications" i need the cards to be double sided with the company logo on the back (attached) the front needs to say my company name, web site, email address, telephone number, and ABN number and electrical license number. I am open to different arrangements of the information but would like the background to be incorporating something electrical or something that looks smart. open to all additional ideas also.

The company colours are orange and grey see logo attached.

Business Name: Corvane Electrical and Communications
Website: corvaneelectricalandcomms.example.com.au
Email: brent@corvaneelectricalandcomms.example.com.au
Telephone(mobile): 0481209736
ABN: 71208349162
Lic No: 418273D

Target Market(s)

Business entities, Project Managers, Accounts, Clients

Industry/Entity Type

Electrician

Contact Information for Business Card

I need a design for business cards, i am an electrical business called "Corvane Electrical and Communications" i need the cards to be double sided with the company logo on the back (attached) the front needs to say my company name

Font styles to use
Serif
Sans Serif

Colors
f37122
5c5c5c

Requirements
Must have
• Must have the Logo on the back open to different ways of it being on the back but had in mind to keep it central but again open to other options
Nice to have
• A real modern cool background that is eye catching yet contemporary
Should not have
• No backgrounds of a light bulb or plug or anything like that

```html
<!DOCTYPE html>
<html lang="en">
<head>
<meta charset="utf-8">
<title>Corvane Electrical and Communications – Business Card</title>
<link rel="stylesheet" href="https://fonts.googleapis.com/css2?family=Mulish:wght@400;500;600;700&display=swap">
<style>
  :root {
    --orange: #f37122;
    --orange-soft: #e9922e;
    --grey: #5c5c5c;
    --charcoal: #3a3a3e;
    --charcoal-deep: #2b2b2f;
    --frost: #f1f2f4;
    --frost-edge: #dfe2e6;
    --light-text: #d9d6d0;
    --page: #e6e4e0;
  }
  * { margin: 0; padding: 0; box-sizing: border-box; }
  html, body {
    width: 1200px; height: 970px; overflow: hidden;
    background: var(--page);
    font-family: "Mulish", sans-serif;
  }
  .card {
    position: absolute; left: 80px; top: 189px;
    width: 1040px; height: 592px;
    background: linear-gradient(135deg, #ffffff 0%, var(--frost) 55%, var(--frost-edge) 100%);
    box-shadow: 0 18px 40px rgba(0,0,0,0.18);
    overflow: hidden;
  }
  .card__shape { position: absolute; inset: 0; }
  .brand {
    position: absolute; left: 56px; top: 150px;
    color: var(--grey); font-weight: 600;
  }
  .brand__name { font-size: 92px; line-height: 1; letter-spacing: 3px; }
  .brand__tagline { font-size: 24px; letter-spacing: 1.5px; margin-top: 14px; text-transform: uppercase; }
  .registration {
    position: absolute; left: 48px; top: 418px;
    font-size: 25px; line-height: 34px; color: var(--grey); font-weight: 500;
  }
  .registration__label { color: var(--orange-soft); }
  .person {
    position: absolute; right: 40px; top: 334px; text-align: right;
  }
  .person__name { font-size: 34px; color: var(--light-text); font-weight: 600; letter-spacing: 0.5px; }
  .person__role { font-size: 27px; color: var(--orange-soft); font-weight: 500; margin-top: -2px; }
  .contacts {
    position: absolute; right: 40px; top: 452px;
    list-style: none; text-align: right;
  }
  .contacts__item {
    display: flex; justify-content: flex-end; align-items: center; gap: 10px;
    height: 36px; font-size: 22px; color: var(--light-text); letter-spacing: 0.5px;
  }
  .contacts__item--phone { font-size: 25px; letter-spacing: 1.5px; }
  .contacts__icon {
    width: 30px; height: 30px; background: var(--orange-soft);
    display: flex; align-items: center; justify-content: center; flex: none;
  }
</style>
</head>
<body>
  <main class="card">
    <svg class="card__shape" width="1040" height="592" viewBox="0 0 1040 592" aria-hidden="true">
      <defs>
        <linearGradient id="panelFade" x1="0" y1="0" x2="1" y2="0.3">
          <stop offset="0" stop-color="#4a4a4f"/>
          <stop offset="1" stop-color="#2b2b2f"/>
        </linearGradient>
      </defs>
      <path d="M912 0 C860 190 660 470 190 592 L1040 592 L1040 0 Z" fill="url(#panelFade)"/>
      <path d="M872 70 C800 250 560 500 120 580 C560 505 815 275 880 60 Z" fill="var(--orange)"/>
    </svg>

    <div class="brand">
      <div class="brand__name">CORVANE</div>
      <div class="brand__tagline">Electrical &amp; Communications</div>
    </div>

    <div class="registration">
      <div><span class="registration__label">Lic No:</span> 418273D</div>
      <div><span class="registration__label">ABN:</span> 71208349162</div>
    </div>

    <div class="person">
      <div class="person__name">Employee Name</div>
      <div class="person__role">Principal</div>
    </div>

    <ul class="contacts">
      <li class="contacts__item contacts__item--phone">0481209736
        <span class="contacts__icon"><svg width="14" height="22" viewBox="0 0 14 22"><rect x="1" y="1" width="12" height="20" rx="2" fill="none" stroke="#3a3a3e" stroke-width="2"/><rect x="3.5" y="4" width="7" height="7" fill="#3a3a3e"/></svg></span>
      </li>
      <li class="contacts__item">brent@corvaneelectricalandcomms.example.com.au
        <span class="contacts__icon"><svg width="22" height="16" viewBox="0 0 22 16"><rect x="1" y="1" width="20" height="14" fill="none" stroke="#3a3a3e" stroke-width="2"/><path d="M1 1 L11 9 L21 1 M1 15 L8 7 M21 15 L14 7" fill="none" stroke="#3a3a3e" stroke-width="1.6"/></svg></span>
      </li>
      <li class="contacts__item">corvaneelectricalandcomms.example.com.au
        <span class="contacts__icon"><svg width="22" height="22" viewBox="0 0 22 22"><circle cx="11" cy="11" r="9" fill="none" stroke="#3a3a3e" stroke-width="1.8"/><ellipse cx="11" cy="11" rx="4" ry="9" fill="none" stroke="#3a3a3e" stroke-width="1.4"/><path d="M2 11 H20 M4 6 H18 M4 16 H18" stroke="#3a3a3e" stroke-width="1.4"/></svg></span>
      </li>
    </ul>
  </main>
</body>
</html>
```